Sophisticated, clean website reflecting my feminine, playful side to sell my abstract art,

I need a website no more than 3 pages to showcase my paintings, a little about me and some contact info. I do abstracts so looking for something a little edgy, yet feminine and current.
Updates

Hi there, These are some artists websites that I Iike: Marnelvoss.com (I like how airy it is) peterwallombry.com garethpolvens.com (I like how it scrolls) I'll need a place for a photo ( a headshot-i do not have it yet so I'll need to be able to upload that later) as well as an area for my bio. Also, it's important that I will be able to upload any new photos and descriptions easily so it should be user friendly. Lastly, I like in a sunny place so would like to have this seem upbeat and playful as that is how i like to paint. thanks-I'm trying to upload my photos now -

Target Market(s)

ppl ages 35-70 who want large scale art for their homes

Industry/Entity Type

art

Coding

Coded - Design and coding required

Number of Pages Required

3 page

Colors

Designer to choose colors to be used in the design.

Requirements
Must have
• photos of my art, a place for my bio, be easy to reach me. tasteful-nothing too "in your face" -my clients are pretty high end and organized. They like clean lines
Nice to have
• sophisticated background, muted tones in the back-similar clean font throughout-no cursive
Should not have
• too many dark areas. Too many blocks of color. Too serious.

```html
<!DOCTYPE html>
<html lang="en">
<head>
<meta charset="utf-8">
<title>Helena Marlowe – Abstract Paintings</title>
<link href="https://fonts.googleapis.com/css2?family=Nunito:wght@300;400&family=Quicksand:wght@400;500&display=swap" rel="stylesheet">
<style>
  :root {
    --ink: #1c1c1c;
    --muted: #6f6f6f;
    --gold: #bfb28f;
    --frame: #d6d0c6;
    --line: #d9d9d9;
    --paper: #ffffff;
    --arrow-box: #1e1b16;
  }
  * { margin: 0; padding: 0; box-sizing: border-box; }
  html, body { width: 1200px; height: 2884px; overflow: hidden; background: var(--paper); }
  body { position: relative; font-family: "Quicksand", sans-serif; color: var(--ink); }
  .abs { position: absolute; }

  /* Header */
  .site-header { position: absolute; left: 0; top: 0; width: 1200px; height: 101px; border-bottom: 2px solid var(--line); }
  .brand { position: absolute; top: 28px; left: 0; width: 1200px; display: flex; justify-content: center; align-items: center; gap: 14px; }
  .brand-mark { width: 44px; height: 44px; border: 3px solid var(--ink); }
  .brand-name { font-family: "Nunito", sans-serif; font-weight: 300; font-size: 44px; letter-spacing: 0.5px; line-height: 1; }

  .main-nav { position: absolute; top: 101px; left: 0; width: 1200px; height: 64px; }
  .main-nav a { position: absolute; top: 20px; transform: translateX(-50%); font-size: 16px; color: #333; text-decoration: none; font-weight: 500; }
  .main-nav a.active::after { content: ""; position: absolute; left: 2px; right: 2px; bottom: -11px; height: 2px; background: var(--ink); }
  .social-handle { display: flex; align-items: center; gap: 6px; font-size: 17px; color: #333; font-weight: 500; }
  .social-dot { width: 32px; height: 32px; border-radius: 50%; background: var(--ink); }

  /* Hero */
  .hero { position: absolute; top: 165px; left: 0; width: 1200px; height: 643px;
    background:
      radial-gradient(ellipse at 20% 35%, #3f9b4c 0%, transparent 45%),
      radial-gradient(ellipse at 55% 25%, #2f8a6e 0%, transparent 40%),
      radial-gradient(ellipse at 85% 70%, #3a3a2e 0%, transparent 40%),
      radial-gradient(ellipse at 40% 80%, #a28a3a 0%, transparent 30%),
      linear-gradient(120deg, #d9dde0 0%, #8fb68c 40%, #1f7b73 70%, #6c6a55 100%); }
  .hero-arrow { position: absolute; top: 272px; width: 40px; height: 44px; }
  .hero-arrow.prev { left: 10px; }
  .hero-arrow.next { right: 10px; }

  /* Section titles */
  .eyebrow { font-family: "Quicksand", sans-serif; font-size: 17px; color: var(--muted); text-transform: uppercase; font-weight: 500; }
  .section-title { font-family: "Nunito", sans-serif; font-weight: 300; font-size: 44px; line-height: 1; letter-spacing: 0.3px; }
  .title-rule { height: 3px; background: var(--gold); width: 64px; }
  .centered { left: 0; width: 1200px; text-align: center; }
  .centered .title-rule { margin: 0 auto; }

  /* About */
  .portrait-frame { position: absolute; left: 54px; top: 921px; width: 416px; height: 413px; }
  .portrait { position: absolute; left: 62px; top: 929px; width: 392px; height: 386px;
    background: linear-gradient(160deg, #f2f2f2 0%, #e6e6e6 60%, #d9d7d3 100%); }
  .about-copy { position: absolute; left: 537px; top: 934px; width: 582px; }
  .about-copy .section-title { margin-top: 6px; }
  .about-copy .title-rule { margin-top: 14px; }
  .bio { margin-top: 32px; font-size: 17px; line-height: 27px; color: #3a3a3a; text-align: justify; }
  .bio + .bio { margin-top: 14px; }

  /* Gallery */
  .gallery-head { position: absolute; top: 1480px; }
  .gallery-head .section-title { margin-top: 6px; }
  .gallery-head .title-rule { margin-top: 12px; }
  .gallery-frame { position: absolute; left: 79px; top: 1593px; width: 1024px; height: 608px; border: 9px solid var(--frame); }
  .gallery-art { position: absolute; left: 98px; top: 1611px; width: 986px; height: 572px;
    background:
      radial-gradient(ellipse at 50% 45%, #1e3f6b 0%, transparent 22%),
      radial-gradient(ellipse at 30% 75%, #b2401e 0%, transparent 18%),
      radial-gradient(ellipse at 85% 50%, #2e4d5c 0%, transparent 25%),
      radial-gradient(ellipse at 15% 15%, #e7e3da 0%, transparent 30%),
      linear-gradient(170deg, #ece8df 0%, #d8a428 35%, #c98f1c 60%, #b9a850 100%); }
  .gallery-arrow { position: absolute; top: 1857px; width: 39px; height: 60px; background: var(--arrow-box); display: flex; align-items: center; justify-content: center; }
  .gallery-arrow.prev { left: 98px; }
  .gallery-arrow.next { left: 1045px; }

  /* Contact */
  .contact-head { position: absolute; top: 2321px; }
  .contact-head .section-title { margin-top: 6px; }
  .contact-head .title-rule { margin-top: 12px; width: 90px; }
  .contact-item { position: absolute; top: 2442px; width: 340px; transform: translateX(-50%); text-align: center; font-size: 23px; font-weight: 500; }
  .contact-icon { width: 65px; height: 65px; border-radius: 50%; background: var(--gold); margin: 0 auto 18px; display: flex; align-items: center; justify-content: center; }

  /* Footer */
  .site-footer { position: absolute; top: 2710px; left: 0; width: 1200px; height: 174px; border-top: 2px solid var(--line); }
  .footer-brand { position: absolute; left: 121px; top: 38px; display: flex; align-items: center; gap: 6px; }
  .footer-brand .brand-mark { width: 44px; height: 44px; }
  .footer-brand .brand-name { font-size: 30px; }
  .footer-nav a { position: absolute; top: 48px; transform: translateX(-50%); font-size: 16px; color: #333; text-decoration: none; font-weight: 500; }
  .footer-social { position: absolute; left: 946px; top: 40px; }
  .footer-social .social-dot { background: var(--gold); }
  .copyright { position: absolute; top: 120px; left: 0; width: 1200px; text-align: center; font-size: 14px; color: #444; }
</style>
</head>
<body>

<header class="site-header">
  <div class="brand">
    <span class="brand-mark"></span>
    <span class="brand-name">HELENA MARLOWE</span>
  </div>
</header>

<nav class="main-nav">
  <a href="#" class="active" style="left:209px">HOME</a>
  <a href="#" style="left:388px">ABOUT ME</a>
  <a href="#" style="left:579px">GALLERY</a>
  <a href="#" style="left:767px">CONTACT</a>
  <a href="#" class="social-handle" style="left:985px;top:14px"><span class="social-dot"></span>@hmarloweart</a>
</nav>

<section class="hero" role="img" aria-label="Featured abstract painting in greens and teal with earthy brushstrokes">
  <svg class="hero-arrow prev" viewBox="0 0 40 44"><polyline points="26,6 12,22 26,38" fill="none" stroke="#fff" stroke-width="5" stroke-linecap="round" stroke-linejoin="round"/></svg>
  <svg class="hero-arrow next" viewBox="0 0 40 44"><polyline points="14,6 28,22 14,38" fill="none" stroke="#fff" stroke-width="5" stroke-linecap="round" stroke-linejoin="round"/></svg>
</section>

<svg class="portrait-frame" viewBox="0 0 416 413">
  <polyline points="330,4 4,4 4,335" fill="none" stroke="#bfb28f" stroke-width="8"/>
  <polyline points="412,78 412,409 86,409" fill="none" stroke="#bfb28f" stroke-width="8"/>
</svg>
<div class="portrait" role="img" aria-label="Artist headshot placeholder"></div>

<section class="about-copy">
  <p class="eyebrow">My Bio</p>
  <h2 class="section-title">ABOUT ME</h2>
  <div class="title-rule"></div>
  <p class="bio">Lorem ipsum dolor sit amet, consectetur adipiscing elit, sed do eiusmod tempor incididunt ut labore et dolore magna aliqua. Ut enim ad minim veniam, quis nostrud exercitation</p>
  <p class="bio">Duis aute irure dolor in reprehenderit in voluptate velit esse cillum dolore eu fugiat nulla pariatur. Excepteur sint occaecat cupidatat non proident, sunt in culpa qui officia deserunt mollit anim id est laborum.Sed ut perspiciatis unde pariatur. Excepteur sint occaecat cupidatat non proident, sunt in culpa qui officia deserunt mollit anim id est laborum.Sed ut perspiciatis un</p>
</section>

<section class="gallery-head centered">
  <p class="eyebrow">My Paintings</p>
  <h2 class="section-title">PAINTING GALLERY</h2>
  <div class="title-rule"></div>
</section>
<div class="gallery-frame"></div>
<div class="gallery-art" role="img" aria-label="Abstract painting in ochre, yellow, deep blue and red"></div>
<div class="gallery-arrow prev"><svg width="16" height="24" viewBox="0 0 16 24"><polyline points="12,3 4,12 12,21" fill="none" stroke="#fff" stroke-width="3" stroke-linecap="round" stroke-linejoin="round"/></svg></div>
<div class="gallery-arrow next"><svg width="16" height="24" viewBox="0 0 16 24"><polyline points="4,3 12,12 4,21" fill="none" stroke="#fff" stroke-width="3" stroke-linecap="round" stroke-linejoin="round"/></svg></div>

<section class="contact-head centered">
  <p class="eyebrow">Get In Touch</p>
  <h2 class="section-title">CONTACT ME</h2>
  <div class="title-rule"></div>
</section>

<div class="contact-item" style="left:268px;top:2433px">
  <div class="contact-icon">
    <svg width="34" height="34" viewBox="0 0 24 24"><path d="M6.6 10.8a15.1 15.1 0 0 0 6.6 6.6l2.2-2.2a1 1 0 0 1 1-.25 11.4 11.4 0 0 0 3.6.57 1 1 0 0 1 1 1V20a1 1 0 0 1-1 1A17 17 0 0 1 3 4a1 1 0 0 1 1-1h3.5a1 1 0 0 1 1 1c0 1.25.2 2.45.57 3.57a1 1 0 0 1-.25 1z" fill="#fff"/></svg>
  </div>
  <span style="position:relative;top:9px">(555) 014 2290</span>
</div>
<div class="contact-item" style="left:607px">
  <div class="contact-icon">
    <svg width="38" height="28" viewBox="0 0 38 28"><rect x="2" y="2" width="34" height="24" rx="2" fill="none" stroke="#fff" stroke-width="3"/><polyline points="2,3 19,16 36,3" fill="none" stroke="#fff" stroke-width="3"/><line x1="2" y1="25" x2="14" y2="13" stroke="#fff" stroke-width="2.5"/><line x1="36" y1="25" x2="24" y2="13" stroke="#fff" stroke-width="2.5"/></svg>
  </div>
  helenamarlowe@studio.com
</div>
<div class="contact-item" style="left:953px">
  <div class="contact-icon"></div>
  @hmarloweart
</div>

<footer class="site-footer">
  <div class="footer-brand">
    <span class="brand-mark"></span>
    <span class="brand-name">HELENA MARLOWE</span>
  </div>
  <nav class="footer-nav">
    <a href="#" style="left:538px">ABOUT ME</a>
    <a href="#" style="left:685px">GALLERY</a>
    <a href="#" style="left:827px">CONTACT</a>
  </nav>
  <a href="#" class="social-handle footer-social"><span class="social-dot"></span>@hmarloweart</a>
  <p class="copyright">© 2022 Helena Marlowe &nbsp;All Rights Reserved</p>
</footer>

</body>
</html>
```